Corvane Holdings , new business card design

investment firm with corporate clients . need double sided business card , vertical and horizontal options ,logo must be clear. prefer pantone colors only and sharp design. website also www.corvane.ae

Khalid Bin Tarrafi
Managing Director
Tel. +971 4 387 2940
Mobile +971 50 518 2403
khalid@corvane.ae
Q-Span Plaza, officw 18-B07, Warqa Gardens, Dubai

Contact Information for Business Card

Khalid Bin Tarrafi
Managing Director

Font styles to use
Serif

Colors

Designer to choose colors to be used in the design.

```html
<!DOCTYPE html>
<html lang="en">
<head>
<meta charset="utf-8">
<title>Corvane Holdings – Business Card</title>
<link rel="stylesheet" href="https://fonts.googleapis.com/css2?family=Roboto:wght@300;400&family=Roboto+Condensed:wght@500&display=swap">
<style>
  :root {
    --backdrop: #8a6a4e;
    --paper: #f4f4f3;
    --ink: #15161a;
    --band: #48739a;
    --band-text: #ffffff;
    --rule: #1c1d22;
    --card-dark: #0c0d12;
    --shadow: rgba(0,0,0,0.45);
  }
  * { margin: 0; padding: 0; box-sizing: border-box; }
  html, body { width: 1200px; height: 960px; overflow: hidden; }
  body {
    position: relative;
    background: var(--backdrop);
    font-family: "Roboto", Arial, sans-serif;
  }
  .card {
    position: absolute;
    width: 598px;
    height: 344px;
    box-shadow: 0 4px 10px var(--shadow);
    overflow: hidden;
  }
  .card--front { left: 322px; top: 108px; background: var(--paper); }
  .card--back { left: 320px; top: 492px; width: 600px; height: 343px; background: var(--card-dark); }

  .wordmark {
    position: absolute;
    left: 0; right: 0;
    text-align: center;
    font-family: "Roboto", Arial, sans-serif;
    font-weight: 300;
    line-height: 1;
  }
  .wordmark__main { display: block; font-size: 46px; letter-spacing: 0.32em; padding-left: 0.32em; }
  .wordmark__sub { display: block; font-size: 15px; letter-spacing: 0.9em; padding-left: 0.9em; margin-top: 8px; }
  .card--front .wordmark { top: 58px; color: var(--ink); }
  .card--back .wordmark { top: 136px; color: #ffffff; }

  .front__divider { position: absolute; left: 0; top: 196px; width: 598px; height: 20px; }
  .front__band {
    position: absolute;
    left: 0; top: 204px;
    width: 598px; height: 140px;
    background: var(--band);
    color: var(--band-text);
  }
  .holder { position: absolute; left: 29px; top: 30px; }
  .holder__name {
    font-family: "Roboto Condensed", Arial Narrow, sans-serif;
    font-weight: 500;
    font-size: 20px;
    letter-spacing: 0.01em;
  }
  .holder__title { font-size: 15px; margin-top: 2px; letter-spacing: 0.02em; }
  .holder__address { font-size: 14px; line-height: 19px; margin-top: 11px; }

  .contacts {
    position: absolute;
    right: 30px; top: 47px;
    list-style: none;
    font-size: 14px;
    line-height: 19px;
    text-align: right;
  }
  .contacts li { display: flex; justify-content: flex-end; align-items: center; gap: 8px; }
  .contacts__web { letter-spacing: 0.16em; }
  .contacts svg { width: 13px; height: 13px; fill: var(--band-text); flex: none; }
</style>
</head>
<body>

<section class="card card--front" aria-label="Business card front">
  <div class="wordmark">
    <span class="wordmark__main">CORVANE</span>
    <span class="wordmark__sub">HOLDINGS</span>
  </div>

  <svg class="front__divider" viewBox="0 0 598 20" aria-hidden="true">
    <polygon points="0,4 68,4 78,16 88,4 598,4 598,8 0,8" fill="var(--rule)"/>
    <polygon points="70,8 78,17 86,8" fill="var(--band)"/>
  </svg>

  <div class="front__band">
    <div class="holder">
      <h1 class="holder__name">KHALID BIN TARRAFI</h1>
      <p class="holder__title">MANAGING DIRECTOR</p>
      <p class="holder__address">Q-Span Plaza, officw 18-B07<br>Warqa Gardens, Dubai</p>
    </div>

    <ul class="contacts">
      <li>+971 4 387 2940
        <svg viewBox="0 0 16 16" aria-label="Phone"><path d="M3.6 1.2l2.2 2.6c.4.5.3 1.1-.1 1.5L4.6 6.4c.8 1.9 2.9 4 4.9 4.9l1.1-1.1c.4-.4 1-.5 1.5-.1l2.6 2.2c.5.4.5 1.1.1 1.6l-1.3 1.3C11 16.7 -1.2 4.6 .9 2.1L2.1 1.1c.4-.4 1.1-.4 1.5.1z"/></svg>
      </li>
      <li>+971 50 518 2403
        <svg viewBox="0 0 16 16" aria-label="Mobile"><path d="M4.5 0h7c.8 0 1.5.7 1.5 1.5v13c0 .8-.7 1.5-1.5 1.5h-7C3.7 16 3 15.3 3 14.5v-13C3 .7 3.7 0 4.5 0zM4.6 2v10.5h6.8V2zM8 13.3a.9.9 0 100 1.8.9.9 0 000-1.8z"/></svg>
      </li>
      <li>khalid@corvane.ae
        <svg viewBox="0 0 16 16" aria-label="Email"><path d="M0 3h16v10H0zM1.5 4.3v.4L8 9l6.5-4.3v-.4zM1.5 6.3v5.2h13V6.3L8 10.6z"/></svg>
      </li>
      <li><span class="contacts__web">www.corvane.ae</span>
        <svg viewBox="0 0 16 16" aria-label="Website"><circle cx="8" cy="8" r="7.5"/><path d="M5 3.5c1 .5 1.8 1.5 1.2 2.5-.6 1-2.2.6-2.6 1.8-.3 1 .9 1.6 1.7 2.1.7.5.5 2 .1 3M11 2.8c-.7 1-.4 2 .6 2.4 1 .4 2 .3 2.6 1.2M10.5 9.5c.8.3 1.2 1.2.9 2.2-.3.8-.1 1.6.4 2" fill="none" stroke="var(--band)" stroke-width="1.2"/></svg>
      </li>
    </ul>
  </div>
</section>

<section class="card card--back" aria-label="Business card back">
  <div class="wordmark">
    <span class="wordmark__main">CORVANE</span>
    <span class="wordmark__sub">HOLDINGS</span>
  </div>
</section>

</body>
</html>
```